Brookvale Building Company - advertisement poster

I am looking to print some canvas signs to advertise my general contracting company, Brookvale Building Company. The sign will measure 6' long x 3' high so the size should match that ratio. I already have a logo icon, which is the Letter 'B' and some trees that I would like to incorporate, see attached. I would also like the to have the following information listed:
1) phone number: 831-555-0172
2) email: brookvalebuildingcompany@mailnest.example
3) website: brookvalebuildingcompany.example
4) Lic#4826130
5) I want to use this text: "BUILD WITH THE B-CREW!"

The ad should be relatively simple and clean. Black and Green are my company colors. I am open to creative ideas!

Target Market(s)

People looking to renovate their homes

Industry/Entity Type

Construction

Colors
59FF00
82FF00
B8FF75
E3FFCB
F4FFEA

Requirements
Must have
• Must have my company logo
Should not have
• No photos or complex graphics

```html
<!DOCTYPE html>
<html lang="en">
<head>
<meta charset="utf-8">
<title>Brookvale Building Company – Sign</title>
<link rel="stylesheet" href="https://fonts.googleapis.com/css2?family=Arimo:wght@400;700&family=Montserrat:wght@500;700;800&display=swap">
<style>
  :root {
    --brand-green: #6cb648;
    --brand-black: #000000;
    --sign-white: #ffffff;
    --ink: #111111;
    --page-bg: #e6e8e5;
  }
  * { box-sizing: border-box; margin: 0; padding: 0; }
  html, body {
    width: 1200px; height: 800px; overflow: hidden;
    background: var(--page-bg);
  }
  .sign {
    position: absolute; left: 40px; top: 120px;
    width: 1120px; height: 560px;
    background: var(--sign-white);
    overflow: hidden;
  }
  .sign__header {
    position: absolute; left: 0; top: 0; width: 100%; height: 197px;
    background: var(--brand-black);
  }
  .brand-name {
    position: absolute; left: 86px; top: 62px;
    display: flex; align-items: center; gap: 16px;
    color: var(--sign-white);
    font-family: "Montserrat", sans-serif; font-weight: 800;
  }
  .brand-name__dot {
    width: 22px; height: 22px; border-radius: 50%;
    background: var(--brand-green);
  }
  .brand-name__text { display: flex; flex-direction: column; line-height: 1; }
  .brand-name__main { font-size: 50px; letter-spacing: 1px; }
  .brand-name__sub { font-size: 17px; letter-spacing: 5.6px; margin-top: 8px; }
  .tagline {
    position: absolute; right: 90px; top: 136px;
    font-family: "Montserrat", sans-serif; font-weight: 800;
    font-size: 27px; letter-spacing: 0.5px;
    color: var(--brand-green);
  }
  .tagline__crew { color: var(--sign-white); }
  .phone {
    position: absolute; left: 72px; top: 218px; width: 960px;
    text-align: center;
    font-family: "Arimo", sans-serif; font-weight: 700;
    font-size: 142px; line-height: 1; letter-spacing: 1px;
    color: var(--brand-green);
  }
  .contacts {
    position: absolute; left: 80px; top: 374px; width: 950px;
    display: flex; justify-content: space-between;
    font-family: "Montserrat", sans-serif; font-weight: 500;
    font-size: 21px; color: var(--ink);
  }
  .contact { display: flex; align-items: center; gap: 7px; }
  .contact__icon { width: 20px; height: 20px; flex: none; }
  .license {
    position: absolute; left: 84px; top: 434px; width: 946px;
    display: flex; align-items: flex-end; gap: 12px;
    font-family: "Arimo", sans-serif; font-weight: 700;
    font-size: 22px; letter-spacing: 5px; color: var(--ink);
  }
  .license__rule { flex: 1; height: 1px; background: var(--ink); margin-bottom: 3px; }
</style>
</head>
<body>
  <main class="sign">
    <header class="sign__header">
      <div class="brand-name">
        <span class="brand-name__dot"></span>
        <span class="brand-name__text">
          <span class="brand-name__main">BROOKVALE</span>
          <span class="brand-name__sub">BUILDING COMPANY</span>
        </span>
      </div>
      <p class="tagline">BUILD WITH THE <span class="tagline__crew">B-CREW!</span></p>
    </header>

    <p class="phone">831-555-0172</p>

    <div class="contacts">
      <span class="contact">
        <svg class="contact__icon" viewBox="0 0 20 20" aria-hidden="true">
          <circle cx="10" cy="10" r="9" fill="var(--ink)"/>
          <rect x="5" y="6.5" width="10" height="7" rx="1" fill="var(--sign-white)"/>
          <path d="M5.5 7 L10 10.5 L14.5 7" fill="none" stroke="var(--ink)" stroke-width="1.3"/>
        </svg>
        brookvalebuildingcompany@mailnest.example
      </span>
      <span class="contact">
        <svg class="contact__icon" viewBox="0 0 20 20" aria-hidden="true" fill="none" stroke="var(--ink)" stroke-width="1.6">
          <circle cx="10" cy="10" r="8"/>
          <ellipse cx="10" cy="10" rx="3.5" ry="8"/>
          <line x1="2" y1="10" x2="18" y2="10"/>
          <line x1="3.5" y1="6" x2="16.5" y2="6"/>
          <line x1="3.5" y1="14" x2="16.5" y2="14"/>
        </svg>
        brookvalebuildingcompany.example
      </span>
    </div>

    <div class="license">
      <span>LIC#4826130</span>
      <span class="license__rule"></span>
    </div>
  </main>
</body>
</html>
```